The Neighbors Together Project

For submission to Lantern Campaign 2024
Need both Color and Black and White Versions
TITLE The Neighbors Together Project
Slogan; "Neighbors Together, one road...one Heart, just a different stride" -JT Pellow copyrights
Logo in Color and Logo in Black and White
Back of flyer will be The Field of Quiet Lanterns poem -JT Pellow
VOTE BLUE 2024 Header or Footer

I just want to thank you all for your participation in The Neighbors Together Project. In the next few days I will be reducing the choices down to 10. Id like for all of you to know Ive enjoyed seeing so many options and views on the Flyer. Mainly, I wanted to say to those who don't make the cut that I appreciate the work you've done.

LM Dorsey

```html
<!DOCTYPE html>
<html lang="en">
<head>
<meta charset="utf-8">
<title>Field of Quiet Lanterns — The Neighbors Together Project</title>
<link href="https://fonts.googleapis.com/css2?family=Bebas+Neue&family=Nunito:wght@700;800&display=swap" rel="stylesheet">
<style>
  :root {
    --paper: #ffffff;
    --red: #d3262d;
    --navy: #1f3566;
    --blush: #f6dcdc;
    --blush-soft: #fbeeee;
  }
  * { box-sizing: border-box; margin: 0; padding: 0; }
  html, body { width: 849px; height: 1200px; overflow: hidden; background: var(--paper); }
  .flyer {
    position: relative;
    width: 849px;
    height: 1200px;
    background: var(--paper);
    overflow: hidden;
    font-family: "Nunito", Arial, sans-serif;
    color: var(--navy);
  }
  .statue-backdrop {
    position: absolute;
    left: 0;
    top: 0;
    width: 330px;
    height: 1200px;
    background: linear-gradient(180deg, var(--blush-soft) 0%, var(--blush) 35%, var(--blush-soft) 75%, rgba(255,255,255,0) 100%);
    opacity: 0.55;
  }
  .brand {
    position: absolute;
    top: 22px;
    left: 0;
    width: 849px;
    display: flex;
    flex-direction: column;
    align-items: center;
    gap: 14px;
  }
  .brand-dot {
    width: 82px;
    height: 82px;
    border-radius: 50%;
    background: var(--red);
  }
  .brand-name {
    font-family: "Nunito", Arial, sans-serif;
    font-weight: 800;
    font-size: 24px;
    color: var(--navy);
    letter-spacing: 0.5px;
  }
  .poem-title {
    position: absolute;
    top: 262px;
    left: 0;
    width: 849px;
    text-align: center;
    font-family: "Bebas Neue", Impact, sans-serif;
    font-size: 88px;
    line-height: 1;
    color: var(--red);
    letter-spacing: 1px;
  }
  .poem-author {
    position: absolute;
    top: 348px;
    left: 0;
    width: 849px;
    text-align: center;
    font-family: "Bebas Neue", Impact, sans-serif;
    font-size: 42px;
    line-height: 1;
    color: var(--navy);
    letter-spacing: 1px;
  }
  .verse {
    position: absolute;
    left: 46px;
    width: 757px;
    text-align: center;
    font-weight: 700;
    font-size: 21.5px;
    line-height: 29px;
  }
  .verse-1 { top: 420px; }
  .verse-2 { top: 536px; }
  .verse-3 { top: 685px; }
  .verse-4 { top: 832px; }
  .verse-5 { top: 980px; }
  .site-url {
    position: absolute;
    top: 1092px;
    left: 0;
    width: 849px;
    text-align: center;
    font-weight: 800;
    font-size: 22px;
    letter-spacing: 0.5px;
    color: var(--navy);
  }
</style>
</head>
<body>
<main class="flyer">
  <div class="statue-backdrop" role="img" aria-label="Faint illustration of a statue holding a raised torch, in pale red tones"></div>

  <header class="brand">
    <span class="brand-dot"></span>
    <span class="brand-name">The Neighbors Together Project</span>
  </header>

  <h1 class="poem-title">Field of Quiet Lanterns</h1>
  <p class="poem-author">By JT Pellow</p>

  <p class="verse verse-1">From wagon trains to aero-planes and spaceships to the moon,forever marching forward to our Yankee-Doodle tune.</p>
  <p class="verse verse-2">We are a land of many colors...red and yellow, black and whte,forever marching forward ever searching for what's right.</p>
  <p class="verse verse-3">We have come from many countries, travelled far across the seas. Leaving friends and loved ones...seeking only to be free.</p>
  <p class="verse verse-4">Free to live, Free to worship, Free to go or Free to stay...living, working all as brothers in this great land... the USA.</p>
  <p class="verse verse-5">We must always pull together, bend an ear to freedom's call.<br>For united we can conquer but divided we will fall.</p>

  <p class="site-url">WWW.NEIGHBORSTOGETHERPROJECT.ORG</p>
</main>
</body>
</html>
```